Stickers By Dwayne needs a website and logo design

I am starting a home business, "Stickers By Dwayne", which I will sell car decals/decals of some sort. I am looking for a creative and professional looking website. I do not want anything too plain/bland, or else I could design it myself. I am up for many options, when it comes to text/colors, and I am not opposed to much. Just nothing too plain. Currently have no logo design to use, may also add this to the project as well. ( I use Wordpress for my site server so it has to be compatible to be used with that website.
Also, I make decals that mainly go on car windows, not as big on car body’s. Also put decals on glassware, and other items. But mainly car windows

• some color, not be bland and white everywhere.

```html
<!DOCTYPE html>
<html lang="en">
<head>
<meta charset="utf-8">
<title>Stickers By Dwayne</title>
<link rel="stylesheet" href="https://fonts.googleapis.com/css2?family=Lobster&family=Roboto:wght@400;500;700&display=swap">
<style>
:root{
  --sky-top:#8fcdeb;
  --sky-bottom:#e9f6fb;
  --green:#5bbf3a;
  --blue:#2f7ea0;
  --yellow:#fcc934;
  --pink:#e7347d;
  --orange:#f26b2b;
  --footer:#2a7ca3;
  --white:#ffffff;
  --ink:#333a3f;
  --script:"Lobster", cursive;
  --sans:"Roboto", Arial, sans-serif;
}
*{box-sizing:border-box;margin:0;padding:0}
html,body{width:1200px;height:3460px;overflow:hidden}
body{font-family:var(--sans);color:var(--white);background:var(--white)}
.page{position:relative;width:1200px;height:3460px;overflow:hidden}
.band{position:absolute;left:0;width:1200px}
.wave{position:absolute;left:0;width:1200px;display:block}

/* header + hero */
.hero{top:0;height:720px;background:linear-gradient(var(--sky-top),var(--sky-bottom) 70%,#ffffff)}
.nav{position:absolute;top:20px;left:0;width:1200px;font-family:var(--script);font-size:19px}
.nav a{position:absolute;color:var(--white);text-decoration:none;white-space:nowrap}
.brand-name{position:absolute;left:500px;top:22px;width:200px;text-align:center;font-family:var(--sans);font-weight:700;font-size:18px;color:var(--white);white-space:nowrap}
.cart{position:absolute;left:1040px;top:3px;font-family:var(--sans);font-size:11px;font-weight:500;display:flex;align-items:center;gap:6px}
.cart i{width:16px;height:16px;border-radius:50%;background:var(--yellow)}
.hero-title{position:absolute;top:180px;width:100%;text-align:center;font-family:var(--script);font-size:52px;font-weight:400;color:var(--blue)}
.btn{position:absolute;height:58px;border-radius:29px;font-size:15px;font-weight:500;letter-spacing:.5px;display:flex;align-items:center;justify-content:center;color:var(--white);text-transform:uppercase}
.btn-pink{background:var(--pink)}
.btn-yellow{background:var(--yellow)}
.btn-orange{background:var(--orange)}
.btn-green{background:var(--green)}
.photo{position:absolute}
.car-photo{border-radius:28px}

/* welcome */
.welcome{top:700px;height:520px;background:var(--green)}
.eyebrow{position:absolute;width:100%;text-align:center;font-size:22px;font-weight:500;letter-spacing:1px;text-transform:uppercase}
.section-title{position:absolute;width:100%;text-align:center;font-family:var(--script);font-size:68px;font-weight:400;line-height:1.2}
.lead{position:absolute;left:330px;width:540px;text-align:center;font-size:15px;line-height:26px;color:#eaf7e2}

/* decals */
.decals{top:1210px;height:1080px;background:var(--blue)}
.tile{position:absolute;top:260px;width:228px;height:228px;border-radius:44px;background:var(--white);border:10px solid}
.tile .photo{left:22px;top:22px;width:164px;height:164px;border-radius:24px}
.arrow{position:absolute;width:30px;height:30px}

/* testimonial */
.testimonial{top:2270px;height:470px;background:var(--yellow)}
.quote{position:absolute;left:410px;top:235px;width:700px;font-size:14px;line-height:25px;color:#fff6d9}
.cite{position:absolute;left:600px;top:360px;font-size:22px;font-weight:500;color:var(--ink)}
.cite span{font-size:14px;font-weight:400;color:#6b6b6b}

/* partners */
.partners{top:2725px;height:140px;background:var(--white);display:flex;align-items:center;justify-content:space-around;padding:0 40px}
.partners span{font-family:var(--sans);font-weight:700;font-size:18px;color:#555;letter-spacing:.5px}

/* contact */
.contact{top:2860px;height:450px;background:var(--pink)}
.field{position:absolute;top:230px;width:415px;height:52px;border-radius:26px;background:var(--white);color:#9a9a9a;font-size:12px;padding-left:26px;display:flex;align-items:center}
.social{position:absolute;left:1123px;width:34px;height:34px;border:2px solid rgba(255,255,255,.8);border-radius:50%}

/* footer */
.footer{top:3300px;height:160px;background:var(--footer)}
.footer-brand{position:absolute;left:60px;top:76px;font-family:var(--sans);font-weight:700;font-size:22px;color:var(--white)}
.footer-note{position:absolute;top:82px;font-size:12px;letter-spacing:.5px;color:#d5ebf5}
</style>
</head>
<body>
<div class="page">

  <section class="band hero">
    <nav class="nav">
      <a style="left:222px">Home</a>
      <a style="left:305px">About Us</a>
      <a style="left:420px">Services</a>
      <a style="left:720px">Car Decals</a>
      <a style="left:845px">Decals</a>
      <a style="left:935px">Contact Us</a>
      <span class="cart"><i></i>MY CART</span>
    </nav>
    <div class="brand-name">Stickers By Dwayne</div>
    <h1 class="hero-title">Stickers By Dwayne</h1>
    <div class="btn btn-pink" style="left:490px;top:264px;width:220px">Get Started</div>
    <div class="photo car-photo" role="img" aria-label="Yellow sedan with orange flame decals on its side" style="left:210px;top:372px;width:760px;height:268px;background:linear-gradient(90deg,#f2d63a 0%,#f3b42e 45%,#ee7a2c 80%,#e4542a 100%)"></div>
  </section>

  <section class="band welcome">
    <svg class="wave" style="top:-60px" height="120" viewBox="0 0 1200 120" preserveAspectRatio="none"><path d="M0 60 C300 0 600 110 900 50 C1050 20 1130 40 1200 60 V120 H0Z" fill="var(--green)"/></svg>
    <div class="eyebrow" style="top:72px">Welcome to</div>
    <h2 class="section-title" style="top:98px">Stickers By Dwayne</h2>
    <p class="lead" style="top:210px">Every decal is cut by hand from durable vinyl, made to hold its colour through sun, rain and car washes. Window lettering, flames, stripes and custom art for glassware and more — tell us your idea and we will bring it to life.</p>
    <div class="btn btn-yellow" style="left:490px;top:390px;width:220px">Learn More</div>
  </section>

  <section class="band decals">
    <svg class="wave" style="top:-60px" height="120" viewBox="0 0 1200 120" preserveAspectRatio="none"><path d="M0 40 C250 100 500 10 800 70 C1000 105 1120 50 1200 40 V120 H0Z" fill="var(--blue)"/></svg>
    <div class="eyebrow" style="top:80px">Cars</div>
    <h2 class="section-title" style="top:102px">Decals</h2>
    <div class="tile" style="left:75px;border-color:var(--pink)"><div class="photo" role="img" aria-label="Orange flame decal" style="background:linear-gradient(#ffd35a,#f26b2b)"></div></div>
    <div class="tile" style="left:345px;border-color:var(--yellow)"><div class="photo" role="img" aria-label="Blue tribal stripe decal" style="background:linear-gradient(#c8d7e8,#3b5f9a)"></div></div>
    <div class="tile" style="left:615px;border-color:var(--green)"><div class="photo" role="img" aria-label="Flaming ball decal" style="background:radial-gradient(#f7b04a,#8a3a1a)"></div></div>
    <div class="tile" style="left:885px;border-color:var(--pink)"><div class="photo" role="img" aria-label="Red and orange flame decal" style="background:linear-gradient(#f8a43b,#d9302a)"></div></div>
    <svg class="arrow" style="left:110px;top:715px" viewBox="0 0 30 30"><path d="M19 7 11 15l8 8" stroke="#fff" stroke-width="3" fill="none"/></svg>
    <svg class="arrow" style="left:1058px;top:715px" viewBox="0 0 30 30"><path d="M11 7l8 8-8 8" stroke="#fff" stroke-width="3" fill="none"/></svg>
    <div class="photo car-photo" role="img" aria-label="Silver sedan with red flame decals" style="left:240px;top:585px;width:720px;height:270px;background:linear-gradient(90deg,#e9edf0 0%,#cfd6dc 55%,#d9a08a 80%,#d8533a 100%)"></div>
    <div class="btn btn-orange" style="left:450px;top:915px;width:300px">Buy Now</div>
  </section>

  <section class="band testimonial">
    <svg class="wave" style="top:-60px" height="120" viewBox="0 0 1200 120" preserveAspectRatio="none"><path d="M0 60 C300 20 500 100 800 60 C1000 30 1100 70 1200 50 V120 H0Z" fill="var(--yellow)"/></svg>
    <div class="eyebrow" style="top:60px">Happy</div>
    <h2 class="section-title" style="top:84px">Customer</h2>
    <svg class="arrow" style="left:32px;top:270px" viewBox="0 0 30 30"><path d="M28 15H4M13 6l-9 9 9 9" stroke="#fff" stroke-width="4" fill="none"/></svg>
    <svg class="arrow" style="left:1138px;top:270px" viewBox="0 0 30 30"><path d="M2 15h24M17 6l9 9-9 9" stroke="#fff" stroke-width="4" fill="none"/></svg>
    <div class="photo" role="img" aria-label="Portrait of a happy customer" style="left:160px;top:190px;width:190px;height:190px;border:10px solid var(--green);border-radius:34px;background:linear-gradient(#f2f2f2,#b8b8b8)"></div>
    <p class="quote">The flame decal for my back window went on without a single bubble and still looks brand new after a whole winter. Fast shipping, friendly help and a great price. I have already ordered a second set for my truck.</p>
    <div class="cite">Marcus Hale &nbsp;<span>| &nbsp;Korvan</span></div>
  </section>

  <section class="band partners">
    <span>KORVAN</span><span>Ellory</span><span>NAKARO</span><span>VANTOR</span><span>QEL</span><span>HALVEX</span><span>OSTRID</span><span>Brennic</span>
  </section>

  <section class="band contact">
    <svg class="wave" style="top:-30px" height="90" viewBox="0 0 1200 90" preserveAspectRatio="none"><path d="M0 40 C300 90 600 0 900 50 C1050 70 1130 40 1200 30 V90 H0Z" fill="var(--pink)"/></svg>
    <div class="eyebrow" style="top:112px">Quick</div>
    <h2 class="section-title" style="top:134px">Contact</h2>
    <div class="field" style="left:183px">NAME *</div>
    <div class="field" style="left:605px">E-MAIL *</div>
    <div class="btn btn-green" style="left:470px;top:322px;width:260px">Submit</div>
    <div class="social" style="top:200px"></div>
    <div class="social" style="top:250px"></div>
    <div class="social" style="top:300px"></div>
    <div class="social" style="top:350px"></div>
  </section>

  <footer class="band footer">
    <svg class="wave" style="top:-40px" height="90" viewBox="0 0 1200 90" preserveAspectRatio="none"><path d="M0 50 C300 10 600 80 900 40 C1050 20 1130 50 1200 40 V90 H0Z" fill="var(--footer)"/></svg>
    <div class="footer-brand">Stickers By Dwayne</div>
    <div class="footer-note" style="left:370px">© 2017 COMPANY NAME | ALL RIGHTS RESERVED</div>
    <div class="footer-note" style="left:900px">TERMS OF CONDITIONS &nbsp;|&nbsp; PRIVACY POLICY</div>
  </footer>

</div>
</body>
</html>
```